Southern Plantskills Academy needs a modern website that oozes professionalism

Our current website is boring and looks like everyone elses. We need a modern website that says we are the best at plant operator training. We use Brontovex and Hiraketo equipment for our training. We train all over Australia in Civil Construction, Mining and Quarrying. We want to be the "Go to" website for all plant operator training in Australia.

Industry/Entity Type

Heavy Machinery Training

Colors
0054AA
0677BA
7BADD7
CADEEF
E8F1F8
FFF300
FFF600
FEFA6F
FFFEC7
FFFEE8

```html
<!DOCTYPE html>
<html lang="en">
<head>
<meta charset="utf-8">
<title>Southern Plantskills Academy</title>
<link href="https://fonts.googleapis.com/css2?family=Montserrat:wght@600;700;800&family=Open+Sans:wght@400;600;700&display=swap" rel="stylesheet">
<style>
:root{
  --navy:#0f2c4c;
  --navy-deep:#0a2038;
  --blue:#0054aa;
  --blue-mid:#0677ba;
  --blue-soft:#7badd7;
  --yellow:#f7c600;
  --yellow-bright:#fff300;
  --grey-bg:#eceef1;
  --text:#333a44;
  --white:#ffffff;
}
*{box-sizing:border-box;margin:0;padding:0}
html,body{width:1200px;height:3292px;overflow:hidden;background:var(--white)}
body{font-family:"Open Sans",Arial,sans-serif;color:var(--text);position:relative}
.section{position:absolute;left:0;width:1200px}
h1,h2,h3,h4{font-family:"Montserrat",Arial,sans-serif}
.btn{display:inline-block;font-family:"Montserrat",Arial,sans-serif;font-weight:700;font-size:15px;padding:14px 26px;border-radius:4px;text-decoration:none}
.btn-yellow{background:var(--yellow);color:var(--navy)}
.btn-dark{background:var(--navy);color:var(--white);border:2px solid var(--yellow)}
.bar{width:60px;height:4px;background:var(--yellow);margin:14px 0 22px}
.bar.center{margin:14px auto 0}

/* header + hero */
.hero{top:0;height:600px;background:linear-gradient(100deg,#0c2440 0%,#17385a 45%,#7a6a3c 75%,#c9a23a 100%)}
.site-header{position:absolute;top:0;left:0;width:1200px;height:100px;background:rgba(10,32,56,.92);display:flex;align-items:center;padding:0 112px}
.brand{display:flex;align-items:center;gap:12px;color:var(--white);font-family:"Montserrat",Arial,sans-serif;font-weight:700;font-size:17px;width:330px;line-height:1.2}
.brand-dot{width:40px;height:40px;border-radius:50%;background:var(--yellow);flex:none}
.main-nav{display:flex;gap:26px;margin-left:auto;align-items:center}
.main-nav a{color:var(--white);font-size:14px;font-weight:600;text-decoration:none}
.main-nav a.active{color:var(--yellow)}
.main-nav .btn{margin-left:16px;padding:12px 22px;font-size:14px}
.hero-title{position:absolute;left:112px;top:212px;color:var(--white);font-size:52px;font-weight:800;line-height:1.12;text-transform:uppercase}
.hero-actions{position:absolute;left:112px;top:428px;display:flex;gap:22px}

/* about */
.about{top:600px;height:560px}
.about-photo{position:absolute;left:112px;top:45px;width:230px;height:435px;background:linear-gradient(180deg,#9bb0c4 0%,#c9a43b 45%,#7d6a3e 80%,#6f6a60 100%)}
.about-copy{position:absolute;left:520px;top:70px;width:570px}
.about-copy h2{font-size:46px;font-weight:800;color:var(--navy)}
.about-copy h3{font-size:24px;font-weight:700;color:var(--navy);margin-bottom:18px}
.about-copy p{font-size:15px;line-height:1.75;margin-bottom:24px}

/* pay later */
.paylater{top:1188px;left:112px;width:976px;height:272px;background:var(--navy);overflow:hidden}
.paylater-copy{position:absolute;left:40px;top:72px;width:440px;color:var(--white)}
.paylater-copy h3{font-size:24px;font-weight:800;text-transform:uppercase;line-height:1.3}
.paylater-copy h3 .hl{color:var(--yellow)}
.paylater-copy p{font-size:15px;line-height:1.6;margin-top:14px}
.paylater-visual{position:absolute;right:0;top:0;width:470px;height:272px;background:linear-gradient(135deg,#3d7fd0 0%,#1f5fb3 55%,#0b3a86 100%)}
.paylater-card{position:absolute;right:40px;top:40px;width:190px;color:var(--white);font-family:"Montserrat",Arial,sans-serif}
.paylater-card .t1{font-weight:700;font-size:19px;line-height:1.3}
.paylater-card .t2{font-weight:800;font-size:22px;line-height:1.25;margin-top:90px}

/* give away */
.giveaway{top:1500px;height:600px}
.giveaway h2{text-align:center;font-size:46px;font-weight:800;color:var(--navy);margin-top:40px}
.giveaway-copy{position:absolute;left:112px;top:196px;width:560px}
.giveaway-copy h3{font-size:30px;font-weight:800;color:var(--navy);text-transform:uppercase;line-height:1.3;margin-bottom:26px}
.giveaway-copy p{font-size:15px;line-height:1.7;margin-bottom:14px}
.giveaway-copy .btn{margin-top:20px}
.prize-boat{position:absolute;left:720px;top:160px;width:368px;height:210px;background:linear-gradient(180deg,#2a5d86 0%,#4b86ae 50%,#1e4f78 100%)}
.prize-bike{position:absolute;left:840px;top:340px;width:250px;height:220px;background:linear-gradient(180deg,#c6c0b6 0%,#6b5b48 55%,#2a2420 100%);border:6px solid var(--white)}

/* trusted partner */
.partner{top:2120px;left:112px;width:976px;height:260px;background:var(--navy);overflow:hidden}
.partner-visual{position:absolute;left:0;top:0;width:420px;height:260px;background:linear-gradient(180deg,#4a6a88 0%,#c79b2e 55%,#5b4a32 100%)}
.partner-copy{position:absolute;left:460px;top:48px;width:470px;color:var(--white)}
.partner-copy h2{font-size:40px;font-weight:800;color:var(--yellow);text-transform:uppercase;line-height:1.1}
.partner-copy p{font-size:15px;line-height:1.6;margin-top:18px}

/* why choose */
.why{top:2440px;height:472px;background:var(--grey-bg)}
.feature{position:absolute;background:var(--navy);color:var(--white);padding:28px 26px;overflow:hidden}
.feature h4{font-size:18px;font-weight:800;text-transform:uppercase;line-height:1.2}
.feature h4 .hl{color:var(--yellow)}
.feature p{font-size:14px;line-height:1.55;margin-top:14px;width:180px}
.feature .badge{position:absolute;right:-20px;bottom:-20px;width:120px;height:120px;border-radius:50%;background:rgba(123,173,215,.18)}
.f1{left:112px;top:60px;width:238px;height:190px}
.f2{left:360px;top:60px;width:234px;height:190px}
.f3{left:112px;top:268px;width:482px;height:150px}
.f3 p{width:240px}
.why-copy{position:absolute;left:660px;top:130px;width:430px}
.why-copy h2{font-size:44px;font-weight:800;color:var(--navy);text-transform:uppercase}
.why-copy p{font-size:15px;line-height:1.75}

/* footer */
.site-footer{top:2912px;height:380px;background:var(--navy-deep);color:var(--white)}
.footer-cols{position:absolute;left:112px;top:52px;width:976px;display:flex;justify-content:space-between}
.footer-col h4{font-size:15px;font-weight:700;text-transform:uppercase;margin-bottom:18px}
.footer-col p,.footer-col li{font-size:14px;line-height:1.85;list-style:none}
.footer-col strong{font-weight:700}
.social{position:absolute;right:112px;top:232px;display:flex;gap:12px}
.social span{width:34px;height:34px;border-radius:50%;background:var(--yellow);display:block}
.footer-band{position:absolute;left:0;top:218px;width:1200px;height:4px;background:var(--yellow)}
.copyright{position:absolute;left:0;top:318px;width:1200px;text-align:center;font-size:13px;color:#c9d3de}
</style>
</head>
<body>

<section class="section hero">
  <div role="img" aria-label="Photo of yellow mining haul trucks at an open-cut site" style="position:absolute;inset:0"></div>
  <header class="site-header">
    <div class="brand"><span class="brand-dot"></span>Southern Plantskills Academy</div>
    <nav class="main-nav">
      <a class="active" href="#">Home</a>
      <a href="#">About</a>
      <a href="#">Courses</a>
      <a href="#">Onsite / Private Courses</a>
      <a href="#">Online Training</a>
      <a href="#">More</a>
      <a class="btn btn-yellow" href="#">Get Started</a>
    </nav>
  </header>
  <h1 class="hero-title">Training and<br>experience you<br>can rely on</h1>
  <div class="hero-actions">
    <a class="btn btn-yellow" href="#">Course Calendar</a>
    <a class="btn btn-dark" href="#">Student Handbook</a>
  </div>
</section>

<section class="section about">
  <div class="about-photo" role="img" aria-label="Photo of a trainee standing beside a yellow wheel loader"></div>
  <div class="about-copy">
    <h2>ABOUT US</h2>
    <div class="bar"></div>
    <h3>We live and breathe safety</h3>
    <p>Southern Plantskills Academy is a versatile team of passionate Health, Safety &amp; Training professionals, all striving towards the common goal of achieving no harm to people, assets and the environment. Our experienced team have been servicing the Bowen Basin mining industry for over 10 years &amp; we have trainers based throughout Queensland. During this time we have established a solid reputation for delivering thorough, timely, and efficient services that are specifically tailored to meet the individual needs of our valued clients within the Mining, Oil &amp; Gas, Civil Construction, Manufacturing and Agricultural sectors.</p>
    <a class="btn btn-yellow" href="#">Course Calendar</a>
  </div>
</section>

<section class="section paylater">
  <div class="paylater-copy">
    <h3>Buy now, pay later with PayLoop<br><span class="hl">Buy what you love now. Pay later.</span></h3>
    <p>Choose and flexibility are on your side.<br>Split your purchases into 4 instalments over 6 weeks.</p>
  </div>
  <div class="paylater-visual" role="img" aria-label="Photo of a phone showing a pay in four checkout screen"></div>
  <div class="paylater-card">
    <div class="t1">PayLoop Pay in 4 is now available.</div>
    <div class="t2">No interest.<br>No late fees.</div>
  </div>
</section>

<section class="section giveaway">
  <h2>GIVE AWAY</h2>
  <div class="bar center"></div>
  <div class="giveaway-copy">
    <h3>Ridgeline motorcycle or a boat package worth $35,000</h3>
    <p>All you have to do is click on the button below and complete a Standard 11 refresher to go into the draw.</p>
    <p><strong>The winner will be announced at the AgriOpen Field Day on Saturday the 22nd of June 2024.</strong></p>
    <a class="btn btn-yellow" href="#">Click Here</a>
  </div>
  <div class="prize-boat" role="img" aria-label="Photo of a speed boat on open water"></div>
  <div class="prize-bike" role="img" aria-label="Photo of a cruiser motorcycle"></div>
</section>

<section class="section partner">
  <div class="partner-visual" role="img" aria-label="Photo of a yellow haul truck at sunset"></div>
  <div class="partner-copy">
    <h2>Your trusted<br>training partner</h2>
    <p>We assist our clients in their ongoing quest to achieve zero harm by providing them with the highest calibre of health and safety management advice and personalised training.</p>
  </div>
</section>

<section class="section why">
  <div class="feature f1"><h4>We are<br><span class="hl">passionate</span></h4><p>We are passionate about Health and Safety.</p><span class="badge"></span></div>
  <div class="feature f2"><h4>We are<br><span class="hl">dependable</span></h4><p>Let us deliver the right training solution for your business.</p><span class="badge"></span></div>
  <div class="feature f3"><h4>Nationally <span class="hl">recognised</span></h4><p>We are accredited to delivery nationally recognised training.</p><span class="badge"></span></div>
  <div class="why-copy">
    <h2>Why choose us?</h2>
    <div class="bar"></div>
    <p>Southern Plantskills Academy consultants have come from the same industries that we consult back to. Our wealth of first hand knowledge and experience enables us to make invaluable contributions to all facets of safety and training in your workplace.</p>
  </div>
</section>

<footer class="section site-footer">
  <div class="footer-cols">
    <div class="footer-col">
      <h4>Contact Information</h4>
      <p><strong>Address :</strong><br>22 Basalt Rd, Ridgefield, QLD 4799<br><strong>Phone :</strong> 1300 482 906<br><strong>Email :</strong> info@spacademy.com.au<br><strong>Southern Plantskills Academy :</strong><br>RTO number #40872</p>
    </div>
    <div class="footer-col">
      <h4>Courses</h4>
      <ul><li>Full Qualifications</li><li>High Risk Licensing</li><li>Plant Operator Tickets</li><li>Short Courses</li></ul>
    </div>
    <div class="footer-col">
      <h4>Student Resources</h4>
      <ul><li>Enrolment Form</li><li>Student Handbook</li><li>Support</li><li>Contact us</li></ul>
    </div>
    <div class="footer-col">
      <h4>Office Time</h4>
      <p>Mon – Fri<br>7:30am to 4:30pm<br>Sat – Sun<br>Holiday</p>
    </div>
  </div>
  <div class="footer-band"></div>
  <div class="social"><span></span><span></span><span></span></div>
  <p class="copyright">2024 Southern Plantskills Academy – RTO number #40872. All Rights Reserved.</p>
</footer>

</body>
</html>
```